New B2C website design to help dads be better dads

DadHarbor is a website to help dads be the “best dad you can be.”

We require our website to be designed into a PSD format, no coding necessary.

The general concept is a two-page design. The first page is the login page, the second page is the home page. Once at the home page, rather than navigating to and from different pages, the user will push and pull through different visual and functional layers of the hierarchy. In theory, this should add to the user experience by having a visual anchor of where they are (through layered pagination) as well as improving loading times since the new information should only be a delta in data load versus a brand new page load.

The general look-and-feel we are going for is clean, simple, minimal. This means that the winning design will show us a good eye for web-optimized typography, good use of white (negative) space, and good use of a visually pleasing grid.

We require a total of 6 page "views" plus the landing page. We note that many of the views are similar to one another.
Landing page
Milestone view
Task view
Content view, articles
Content view, products
Search view
What's new view

Please review all of the additional information provided as well as the attachments for examples.

We provide the following websites as good references for:

Typography:
http://example-kelvorn.com/journal/

Use of white space:
http://www.trenvaskit.com/
http://moldrefin.com/

Example for “scrolling” page concept as well as good balance of color, typography, and white space:
http://www.qorbitalmeet.eu/

Please contact us with questions so that we can guide your design effort.
Updates

Hello designers,

The following information is added to help guide the design process:

1.  For the text dialogue below the landing page, please assume the following word count:
"why are we making dad harbor?": 250 words
"who are we?" 200 words
"what's the deal with the penguin logo?" 300 words

For the social media links, please see http://www.gravelplumbs.com/
Notice the floating "social" bar that is always to the right.  This is the concept we are going for, please try to implement this as you see fit. 

Target Market(s)

Fathers of young children ages 0-6 years old.

Industry/Entity Type

Product

Font styles to use
Sans Serif

Requirements
Must have
• Clean lines, minimal design concept

Incorporation of our logo (see attached document)

Header content is static for all views after landing page, see example

This page WILL be responsive, please keep that in mind when designing
The timeline bar should be to the left, with the timeline bar’s “milestones” also being responsive.

Designer is free to suggest font types, but any fonts used must be royalty-free and web-optimized. We request a minimum number of font types as well as fonts that load relatively fast. We reinforce that visually appealing typography is a significant factor in the winning design choice.

While we are not expecting the winning design to include code, please keep in mind that the final implementation needs to be optimized for desktop, tablet, and mobile platforms.

If you are using stock photography that is not generated by you, please provide where/how we can obtain imagery, as well as price.

All custom graphics must be available in original formats; Photoshop/GIMP layered files for layout design, and vector formats for logos, icons and other graphical elements.

Please incorporate “Blue” into design elements as you see fit, as the RGB 67 74 169 Blue is the primary color used in our brand. The complement to this blue is 255 202 0, a brownish orange. Feel free to use this color as well, although please keep it to a lesser amount.

Background color is your choice, do not feel the need to use the grey.
Should not have
• Excessive graphical content such that it affects loading times

Excessive use of too many font types such that it affects loading times

```html
<!DOCTYPE html>
<html lang="en">
<head>
<meta charset="utf-8">
<title>DadHarbor – Prepare for the baby arrival</title>
<link rel="stylesheet" href="https://fonts.googleapis.com/css2?family=PT+Sans:wght@400;700&family=Roboto+Slab:wght@400;600&display=swap">
<style>
:root{
  --brand-blue:#434aa9;
  --brand-gold:#ffca00;
  --button-gold:#f8b81f;
  --welcome-orange:#e09a1c;
  --ink:#333;
  --muted:#6d6d6d;
  --line:#d6d6d6;
  --soft-line:#e6e6e6;
  --page:#f7f7f7;
  --white:#fff;
  --tab:#e2e2e2;
  --star:#f5c518;
}
*{box-sizing:border-box;margin:0;padding:0}
html,body{width:891px;height:1200px;overflow:hidden}
body{position:relative;background:var(--page);font-family:"PT Sans",Arial,sans-serif;color:var(--ink)}
.site-header{position:absolute;left:0;top:0;width:891px;height:139px;background:var(--white);border-bottom:1px solid var(--line)}
.brand{position:absolute;left:74px;top:92px;display:flex;align-items:center;gap:6px;font:700 17px "PT Sans",Arial,sans-serif;color:var(--brand-blue);letter-spacing:.5px}
.brand-mark{width:12px;height:12px;background:var(--brand-blue)}
.welcome{position:absolute;right:75px;top:13px;font:400 19px "Roboto Slab",Georgia,serif;color:var(--welcome-orange)}
.search{position:absolute;left:522px;top:58px;display:flex;gap:5px}
.search-input{width:227px;height:25px;border:1px solid var(--line);background:var(--white);font-size:10px;color:#999;padding:6px 10px}
.search-button{width:57px;height:26px;background:var(--button-gold);border:1px solid #e9a80f;border-radius:2px;font:400 11px "PT Sans",sans-serif;color:#6b4a00;display:flex;align-items:center;justify-content:center}
.account-bar{position:absolute;left:522px;top:104px;display:flex;align-items:center;font-size:12px}
.score{color:var(--brand-blue);display:flex;align-items:center;gap:6px}
.account-links{margin-left:31px;color:var(--muted);font-size:11.5px}
.account-links span{margin:0 6px;color:#aaa}
.page-title{position:absolute;left:74px;top:161px;font:400 21px "Roboto Slab",Georgia,serif;color:#555}
.sort{position:absolute;left:673px;top:164px;display:flex;align-items:center;gap:7px;font-size:9.5px;color:var(--muted)}
.sort-select{width:102px;height:21px;border:1px solid var(--line);background:var(--white);color:var(--ink);padding:4px 8px;position:relative}
.sort-select::after{content:"";position:absolute;right:8px;top:8px;border:4px solid transparent;border-top-color:#444}
.title-rule{position:absolute;left:74px;top:211px;width:743px;border-top:1px solid var(--line)}
.sidebar{position:absolute;left:74px;top:211px;width:181px;height:968px;border:1px solid var(--line);border-top:0;background:var(--white)}
.task-list{list-style:none;margin:4px 7px 0 8px}
.task{height:32.6px;border-bottom:1px solid var(--soft-line);display:flex;align-items:center;gap:9px;padding-left:12px;font-size:11.5px;color:#444}
.checkbox{width:9px;height:9px;border:1px solid #999;background:#eee;position:relative}
.checkbox.done::after{content:"";position:absolute;left:2px;top:0;width:3px;height:5px;border:solid var(--brand-blue);border-width:0 1.5px 1.5px 0;transform:rotate(40deg)}
.timeline{position:absolute;left:25px;top:291px;width:131px}
.year{height:30px;background:var(--tab);border:1px solid #ccc;border-radius:2px;display:flex;align-items:center;justify-content:center;font-size:14px;color:#333;margin-bottom:1.8px}
.months{margin:1px 0 8px}
.month{height:28px;border:1px solid var(--line);background:var(--white);display:flex;align-items:center;justify-content:center;font-size:10.5px;color:var(--muted);margin-bottom:1.5px}
.intro{position:absolute;left:284px;top:230px;width:522px;text-align:center}
.intro h2{font:600 15px "Roboto Slab",Georgia,serif;color:#222}
.intro p{font:400 11.5px "Roboto Slab",Georgia,serif;color:#444;margin-top:6px}
.cards{position:absolute;left:284px;top:294px;display:grid;grid-template-columns:251px 251px;column-gap:21px;row-gap:23px}
.card{height:280px;border:1px solid var(--line);background:var(--white);padding:4px}
.card-media{position:relative;height:136px}
.badge{position:absolute;right:1px;bottom:1px;width:29px;height:33px;background:var(--brand-gold);display:flex;align-items:center;justify-content:center}
.card-title{font:400 12.5px/17px "Roboto Slab",Georgia,serif;color:var(--brand-blue);margin:12px 8px 0}
.rating{display:flex;align-items:center;gap:1px;margin:8px 8px 0;font-size:11px;color:#555}
.rating .count{margin-left:8px}
.card-text{font-size:11px;line-height:17px;color:#666;margin:10px 8px 0}
.read-more{color:var(--brand-blue);white-space:nowrap}
.read-more svg{vertical-align:-1px;margin:0 2px 0 6px}
.footer-rule{position:absolute;left:0;top:1197px;width:891px;border-top:1px solid var(--line)}
</style>
</head>
<body>
<svg width="0" height="0" style="position:absolute">
  <defs>
    <symbol id="star" viewBox="0 0 20 20"><path d="M10 1l2.7 6 6.3.6-4.8 4.3 1.4 6.3L10 15l-5.6 3.2 1.4-6.3L1 7.6 7.3 7z"/></symbol>
    <linearGradient id="half"><stop offset="50%" stop-color="#f5c518"/><stop offset="50%" stop-color="#fff"/></linearGradient>
    <symbol id="stars" viewBox="0 0 80 16">
      <use href="#star" x="0" width="16" height="16" fill="#f5c518"/>
      <use href="#star" x="16" width="16" height="16" fill="#f5c518"/>
      <use href="#star" x="32" width="16" height="16" fill="#f5c518"/>
      <use href="#star" x="48" width="16" height="16" fill="#f5c518"/>
      <use href="#star" x="64" width="16" height="16" fill="url(#half)" stroke="#f5c518" stroke-width="1.2"/>
    </symbol>
    <symbol id="doc" viewBox="0 0 20 24"><path d="M4 2h10l4 4v15a1 1 0 0 1-1 1H4a1 1 0 0 1-1-1V3a1 1 0 0 1 1-1z" fill="#111"/><path d="M3 18c3-1 10-1 15 3" stroke="#ffca00" stroke-width="1.4" fill="none"/></symbol>
    <symbol id="cart" viewBox="0 0 24 20"><path d="M1 2h4l3 11h12l2-8H7" fill="none" stroke="#111" stroke-width="2"/><path d="M8 7h12M9 10h10" stroke="#111" stroke-width="1.4"/><circle cx="9" cy="17" r="1.8" fill="#111"/><circle cx="18" cy="17" r="1.8" fill="#111"/></symbol>
    <symbol id="plus" viewBox="0 0 10 10"><circle cx="5" cy="5" r="5" fill="#434aa9"/><path d="M5 2.5v5M2.5 5h5" stroke="#fff" stroke-width="1.4"/></symbol>
  </defs>
</svg>

<header class="site-header">
  <div class="brand"><span class="brand-mark"></span>DADHARBOR</div>
  <p class="welcome">Welcome Greg, what would you like to do today?</p>
  <div class="search"><div class="search-input">Keyword...</div><div class="search-button">SEARCH</div></div>
  <div class="account-bar">
    <span class="score"><svg width="10" height="9" viewBox="0 0 10 9"><path d="M5 9L1 5A2.4 2.4 0 0 1 5 1.6 2.4 2.4 0 0 1 9 5z" fill="#434aa9"/></svg>Super Dad Score: 10,500</span>
    <span class="account-links">My Account<span>|</span>Log out</span>
  </div>
</header>

<h1 class="page-title">Prepare for the baby arrival</h1>
<div class="sort">Sort by :<div class="sort-select">Most recent</div></div>
<div class="title-rule"></div>

<aside class="sidebar">
  <ul class="task-list">
    <li class="task"><span class="checkbox"></span>Buy a crib</li>
    <li class="task"><span class="checkbox"></span>Assemble the crib</li>
    <li class="task"><span class="checkbox"></span>Buy a stroller</li>
    <li class="task"><span class="checkbox done"></span>Buy a carseat</li>
    <li class="task"><span class="checkbox"></span>Install a carseat</li>
    <li class="task"><span class="checkbox"></span>Learn to change a diaper</li>
    <li class="task"><span class="checkbox"></span>Learn to hold a baby</li>
    <li class="task"><span class="checkbox"></span>Set a fedding schedule</li>
  </ul>
  <nav class="timeline">
    <div class="year">2013</div>
    <div class="months">
      <div class="month">November</div><div class="month">October</div><div class="month">September</div>
      <div class="month">August</div><div class="month">July</div><div class="month">June</div>
      <div class="month">May</div><div class="month">April</div><div class="month">March</div>
      <div class="month">February</div><div class="month">January</div>
    </div>
    <div class="year">2012</div><div class="year">2011</div><div class="year">2010</div>
    <div class="year">2009</div><div class="year">2008</div><div class="year">2007</div>
    <div class="year">2006</div><div class="year">2005</div><div class="year">2004</div>
  </nav>
</aside>

<section class="intro">
  <h2>Your big day is almost here! Do you have your go-back packed?</h2>
  <p>Do you have your routes (plural!) to the hospital mapped out? Lots to do, not much time!</p>
</section>

<main class="cards">
  <article class="card">
    <div class="card-media" role="img" aria-label="Baby in a car seat playing with a hanging toy" style="background:linear-gradient(135deg,#2a2a2e,#8a8d92 55%,#c9ccd0)"><span class="badge"><svg width="18" height="22"><use href="#doc"/></svg></span></div>
    <h3 class="card-title">Pellentesque habitant morbi tristique senectus et netus</h3>
    <div class="rating"><svg width="80" height="16"><use href="#stars"/></svg><span class="count">3,121 ratings</span></div>
    <p class="card-text">I went out to buy my first car seat and had to earn my PhD in car seats, Newtonian physics, and anti-stain technology··· <span class="read-more"><svg width="10" height="10"><use href="#plus"/></svg>Read More</span></p>
  </article>
  <article class="card">
    <div class="card-media" role="img" aria-label="Smiling baby in an infant car seat" style="background:linear-gradient(135deg,#6b5a48,#a99a86 50%,#d8cfc2)"><span class="badge"><svg width="22" height="18"><use href="#cart"/></svg></span></div>
    <h3 class="card-title">Pellentesque habitant morbi tristique senectus et netus</h3>
    <div class="rating"><svg width="80" height="16"><use href="#stars"/></svg><span class="count">3,121 ratings</span></div>
    <p class="card-text">I went out to buy my first car seat and had to earn my PhD in car seats, Newtonian physics, and anti-stain technology··· <span class="read-more"><svg width="10" height="10"><use href="#plus"/></svg>Read More</span></p>
  </article>
  <article class="card">
    <div class="card-media" role="img" aria-label="Toddler laughing in a car seat on a leather back seat" style="background:linear-gradient(135deg,#8c3a1c,#c27a4a 50%,#e2b98e)"><span class="badge"><svg width="18" height="22"><use href="#doc"/></svg></span></div>
    <h3 class="card-title">Pellentesque habitant morbi tristique senectus et netus</h3>
    <div class="rating"><svg width="80" height="16"><use href="#stars"/></svg><span class="count">3,121 ratings</span></div>
    <p class="card-text">I went out to buy my first car seat and had to earn my PhD in car seats, Newtonian physics, and anti-stain technology··· <span class="read-more"><svg width="10" height="10"><use href="#plus"/></svg>Read More</span></p>
  </article>
  <article class="card">
    <div class="card-media" role="img" aria-label="Baby strapped into a grey and orange car seat" style="background:linear-gradient(180deg,#3b3e44,#55585e 50%,#c98a6a)"><span class="badge"><svg width="22" height="18"><use href="#cart"/></svg></span></div>
    <h3 class="card-title">Pellentesque habitant morbi tristique senectus et netus</h3>
    <div class="rating"><svg width="80" height="16"><use href="#stars"/></svg><span class="count">3,121 ratings</span></div>
    <p class="card-text">I went out to buy my first car seat and had to earn my PhD in car seats, Newtonian physics, and anti-stain technology··· <span class="read-more"><svg width="10" height="10"><use href="#plus"/></svg>Read More</span></p>
  </article>
  <article class="card">
    <div class="card-media" role="img" aria-label="Baby buckled in with a seat belt" style="background:linear-gradient(135deg,#4c5458,#7e8a8c 50%,#aab4b4)"><span class="badge"><svg width="18" height="22"><use href="#doc"/></svg></span></div>
    <h3 class="card-title">Pellentesque habitant morbi tristique senectus et netus</h3>
    <div class="rating"><svg width="80" height="16"><use href="#stars"/></svg><span class="count">3,121 ratings</span></div>
    <p class="card-text">I went out to buy my first car seat and had to earn my PhD in car seats, Newtonian physics, and anti-stain technology··· <span class="read-more"><svg width="10" height="10"><use href="#plus"/></svg>Read More</span></p>
  </article>
  <article class="card">
    <div class="card-media" role="img" aria-label="Baby sleeping in a car seat" style="background:linear-gradient(135deg,#3a2a22,#8f7664 50%,#cdb5a4)"><span class="badge"><svg width="22" height="18"><use href="#cart"/></svg></span></div>
    <h3 class="card-title">Pellentesque habitant morbi tristique senectus et netus</h3>
    <div class="rating"><svg width="80" height="16"><use href="#stars"/></svg><span class="count">3,121 ratings</span></div>
    <p class="card-text">I went out to buy my first car seat and had to earn my PhD in car seats, Newtonian physics, and anti-stain technology··· <span class="read-more"><svg width="10" height="10"><use href="#plus"/></svg>Read More</span></p>
  </article>
</main>
<div class="footer-rule"></div>
</body>
</html>
```